RW Holloway LLC Business Card - Civil Engineering & Consulting Firm

We need a Business Card that is elegant, and masculine.  It is our Professional Civil Engineering & Consulting Company located in San Antonio TX (Not s construction or builder firm- no gears & no tool images please). We provide civil engineering services including  commercial site plans, grading and drainage plans, utility plans, hydraulics and hydrology, land planning, utility coordination, and other general civil engineering services related to commercial and residential development.
We have 2 existing Logos. We would like to convey reliability, strength, trustworthiness and attention to detail.  Blues and orange tones as per logo We are OK with the use of a darker blue in the mix.  We have 2 logo versions - Full Company Name Logo to go on the back of card, & Small Icon Logo for the front w/ personal Info.

Target Market(s)
Architects, Real Estate Developers, Other Strctural Engineers, Surveyers, General Contractors
Industry/Entity Type
Professional Civil Engineering
Contact Information for Business Card
Name, Position, Address, Cell & Office #, email, and company website
Font styles to use
Other font styles liked:
- Avian
Requirements
Should not have
- No Tools, No Gears, no Cranes, or Construction Equipment.

```html
<!DOCTYPE html>
<html lang="en">
<head>
<meta charset="utf-8">
<title>RW Holloway LLC Business Card</title>
<link href="https://fonts.googleapis.com/css2?family=Montserrat:wght@400;500;700&display=swap" rel="stylesheet">
<style>
  :root {
    --bg: #bdbdbd;
    --paper: #ffffff;
    --blue: #7aaad6;
    --orange: #ee8f2c;
    --ink: #1c1c1c;
    --back-blue: #7f9fbd;
    --back-orange: #e0964c;
  }
  * { margin: 0; padding: 0; box-sizing: border-box; }
  html, body { width: 1200px; height: 813px; overflow: hidden; }
  body {
    background: var(--bg);
    font-family: "Montserrat", sans-serif;
    position: relative;
  }
  .card {
    position: absolute;
    top: 252px;
    width: 540px;
    height: 309px;
    box-shadow: 0 10px 28px rgba(0,0,0,0.35);
    overflow: hidden;
  }
  .card-front { left: 40px; background: var(--paper); }
  .card-back {
    left: 620px;
    background: linear-gradient(150deg, var(--back-blue) 0%, #a9a39c 50%, var(--back-orange) 100%);
    display: flex;
    align-items: center;
    justify-content: center;
  }
  .edge-art { position: absolute; inset: 0; }
  .front-brand {
    position: absolute;
    top: 58px;
    right: 40px;
    display: flex;
    align-items: center;
    gap: 8px;
    font-size: 17px;
    font-weight: 700;
    color: var(--orange);
    letter-spacing: 0.5px;
  }
  .brand-square { width: 12px; height: 12px; background: var(--blue); }
  .contact {
    position: absolute;
    left: 34px;
    top: 128px;
    color: var(--ink);
    font-size: 13px;
    line-height: 1.35;
  }
  .contact-name {
    color: var(--orange);
    font-weight: 700;
    font-size: 16px;
    letter-spacing: 0.5px;
    text-transform: uppercase;
  }
  .contact-role { margin-bottom: 8px; }
  .contact-address { margin-bottom: 8px; }
  .contact-line { display: flex; align-items: center; gap: 8px; }
  .contact-icon { width: 13px; height: 13px; flex: none; }
  .back-name {
    color: #ffffff;
    font-size: 38px;
    font-weight: 500;
    letter-spacing: 3px;
    text-transform: uppercase;
  }
</style>
</head>
<body>
  <section class="card card-front">
    <svg class="edge-art" width="540" height="309" viewBox="0 0 540 309">
      <defs>
        <linearGradient id="edge-gradient" x1="0" y1="0" x2="1" y2="0">
          <stop offset="0" stop-color="#7aaad6"/>
          <stop offset="0.45" stop-color="#7aaad6"/>
          <stop offset="0.75" stop-color="#ee8f2c"/>
          <stop offset="1" stop-color="#ee8f2c"/>
        </linearGradient>
      </defs>
      <polygon points="0,0 540,0 540,10 200,10 185,30 0,30" fill="url(#edge-gradient)"/>
      <polygon points="205,17 540,17 540,22 200,22" fill="#7aaad6"/>
      <polygon points="0,309 540,309 540,279 375,279 360,299 0,299" fill="url(#edge-gradient)"/>
      <polygon points="0,287 345,287 340,292 0,292" fill="#7aaad6"/>
    </svg>

    <div class="front-brand"><span class="brand-square"></span>RW Holloway LLC</div>

    <div class="contact">
      <div class="contact-name">Dane Whitfield</div>
      <div class="contact-role">Co-Founder</div>
      <div class="contact-address">4180 Calloway Road<br>Suite 210 Alamo Park</div>
      <div class="contact-line">
        <svg class="contact-icon" viewBox="0 0 16 16"><circle cx="8" cy="8" r="8" fill="#ee8f2c"/><path d="M5 4.5 L6.5 4.5 L7.2 6.5 L6.3 7.3 Q7.3 9.2 8.7 9.8 L9.5 8.9 L11.5 9.6 L11.5 11 Q8 11.8 5.6 8.6 Q4.4 6.6 5 4.5Z" fill="#fff"/></svg>
        <span>555-214-0186</span>
      </div>
      <div class="contact-line">
        <svg class="contact-icon" viewBox="0 0 16 16"><circle cx="8" cy="8" r="8" fill="#ee8f2c"/><rect x="4.5" y="6.5" width="7" height="5" rx="1" fill="#fff"/><rect x="4" y="4.5" width="8" height="1.6" rx="0.8" fill="#fff"/></svg>
        <span>555-214-0342</span>
      </div>
      <div class="contact-line">
        <svg class="contact-icon" viewBox="0 0 16 16"><circle cx="8" cy="8" r="8" fill="#ee8f2c"/><rect x="4" y="5" width="8" height="6" fill="#fff"/><path d="M4 5 L8 8.5 L12 5" fill="none" stroke="#ee8f2c" stroke-width="1"/></svg>
        <span>info@rwholloway</span>
      </div>
      <div class="contact-line">
        <svg class="contact-icon" viewBox="0 0 16 16"><circle cx="8" cy="8" r="8" fill="#ee8f2c"/><circle cx="8" cy="8" r="4" fill="none" stroke="#fff" stroke-width="1"/><ellipse cx="8" cy="8" rx="1.8" ry="4" fill="none" stroke="#fff" stroke-width="1"/><line x1="4" y1="8" x2="12" y2="8" stroke="#fff" stroke-width="1"/></svg>
        <span>www.rwholloway.com</span>
      </div>
    </div>
  </section>

  <section class="card card-back">
    <div class="back-name">RW Holloway LLC</div>
  </section>
</body>
</html>
```